Finiding oppertunites in Real Estate 6.15.20

size of ad 7” x 9.6”
1-I like the ad to stand out and attract people's attention.
2-you should be able to see the text of the ad clearly .. see the attachment anything in yellow is instructions.
3-the list of topics should not be the main part of the ad
4-if you decide you want a picture or vector of a person .. (you decide)
then it should be a white male about 25-30 years old wearing a solid white or blue shirt and not long hair.
5-leave 1 inch for footer
see attachment
Good luck

Target Market(s)

potential male students 25-35 years of age

Industry/Entity Type

Education

Requirements
Must have
• will stand out and people would want to see it.
should be able to read the words of ad
Nice to have
• how to make money in real estate on one line

```html
<!DOCTYPE html>
<html lang="en">
<head>
<meta charset="utf-8">
<title>Real Estate Career Course Flyer</title>
<link rel="stylesheet" href="https://fonts.googleapis.com/css2?family=Anton&family=Archivo+Black&family=Arimo:wght@400;700&family=Bangers&display=swap">
<style>
  :root {
    --blue: #0a3fbf;
    --blue-deep: #0033a8;
    --ink: #111111;
    --paper: #ffffff;
    --stage: #e4e4e6;
    --footer-text: #6f8fe0;
    --photo-light: #eef1f6;
    --photo-mid: #b9c4d4;
    --burst-green: #3bb57a;
    --burst-orange: #f39a1f;
  }
  * { box-sizing: border-box; margin: 0; padding: 0; }
  html, body { width: 1200px; height: 1200px; overflow: hidden; background: var(--stage); }
  .flyer {
    position: absolute; left: 185px; top: 30px;
    width: 830px; height: 1140px;
    background: var(--paper); overflow: hidden;
    font-family: "Arimo", Arial, sans-serif; color: var(--ink);
    box-shadow: 0 10px 30px rgba(0,0,0,.18);
  }
  .header-photo {
    position: absolute; left: 0; top: 0; width: 830px; height: 330px;
    background: linear-gradient(90deg, var(--photo-mid) 0%, var(--photo-light) 45%, #f6f7fa 100%);
  }
  .person-photo {
    position: absolute; left: 20px; top: 60px; width: 200px; height: 258px;
    background: linear-gradient(180deg, #c9ccd3 0%, #3a5a94 60%, #27406e 100%);
  }
  .roofline { position: absolute; left: 0; top: 0; }
  .title-block { position: absolute; left: 240px; top: 80px; width: 510px; }
  .course-title {
    font-family: "Archivo Black", sans-serif; color: var(--blue);
    font-size: 34px; line-height: 1.05; white-space: nowrap;
  }
  .course-subtitle { font-size: 22px; margin-top: 6px; font-weight: 400; white-space: nowrap; }
  .intro {
    position: absolute; left: 115px; top: 345px; width: 600px;
    text-align: center; font-size: 26px; line-height: 1.15;
  }
  .headline {
    position: absolute; left: 30px; top: 418px; width: 770px;
    font-family: "Anton", sans-serif; font-size: 44px; line-height: 1.1;
    text-align: center; text-transform: uppercase; letter-spacing: .5px;
  }
  .headline .accent { color: var(--blue); }
  .schedule { position: absolute; left: 60px; top: 548px; }
  .schedule .line { font-size: 34px; line-height: 1.05; }
  .schedule .start-date {
    font-family: "Anton", sans-serif; color: var(--blue);
    font-size: 108px; line-height: 1.1; letter-spacing: 1px;
  }
  .burst {
    position: absolute; left: 440px; top: 525px; width: 360px; height: 255px;
    border-radius: 50%;
    background: radial-gradient(ellipse at 55% 50%, var(--burst-orange) 0%, var(--burst-green) 45%, rgba(255,255,255,0) 72%);
  }
  .burst-label {
    position: absolute; left: 470px; top: 580px; width: 300px;
    font-family: "Bangers", cursive; color: var(--paper);
    font-size: 58px; line-height: .95; text-align: center; letter-spacing: 2px;
    transform: rotate(-12deg);
  }
  .topics-bar {
    position: absolute; left: 60px; top: 762px; width: 400px; height: 40px;
    background: var(--ink); color: var(--paper);
    font-size: 19px; letter-spacing: 1px; line-height: 40px; text-align: center;
  }
  .topics { position: absolute; list-style: none; font-size: 19px; line-height: 1.2; }
  .topics li::before {
    content: ""; display: inline-block; width: 8px; height: 8px; border-radius: 50%;
    background: var(--blue); margin-right: 10px; vertical-align: middle;
  }
  .topics-left { left: 70px; top: 812px; }
  .topics-right { left: 490px; top: 792px; }
  .footer {
    position: absolute; left: 0; bottom: 0; width: 830px; height: 119px;
    background: var(--blue-deep); color: var(--footer-text);
    font-size: 64px; letter-spacing: 4px; text-align: center; line-height: 119px;
  }
</style>
</head>
<body>
<main class="flyer">
  <div class="header-photo"></div>
  <div class="person-photo" role="img" aria-label="Photo of a smiling young businessman in a blue suit giving a thumbs up"></div>
  <svg class="roofline" width="830" height="340" viewBox="0 0 830 340" aria-hidden="true">
    <polygon points="0,340 0,318 230,318 230,262 765,262 765,180 800,180 800,232 830,232 830,340" fill="#ffffff"/>
    <polyline points="0,318 230,318 230,262 765,262 765,180 800,180 800,232 830,232" fill="none" stroke="#0a3fbf" stroke-width="14"/>
  </svg>
  <div class="title-block">
    <h1 class="course-title">Real Estate Career Course</h1>
    <p class="course-subtitle">How to Make Money In In Real Estate?</p>
  </div>
  <p class="intro">For those who have started or would like to go into Real Estate</p>
  <h2 class="headline">
    <span class="accent">An</span> Investment <span class="accent">in Knowledge Opens</span><br>
    <span class="accent">Up Untold</span> Opportunities
  </h2>
  <div class="schedule">
    <p class="line">12 session course</p>
    <p class="line">Classes starting</p>
    <p class="start-date">JUNE,16</p>
  </div>
  <div class="burst" role="img" aria-label="Comic-style explosion burst with halftone dots and stars"></div>
  <p class="burst-label">REMOTE<br>SESSIONS</p>
  <div class="topics-bar">A PARTIAL LISTING OF TOPICS</div>
  <ul class="topics topics-left">
    <li>Single-family</li>
    <li>Multifamily</li>
    <li>Management</li>
    <li>Real Estate Concepts</li>
    <li>Real Estate law</li>
    <li>Investment properties</li>
    <li>Foreclosures</li>
  </ul>
  <ul class="topics topics-right">
    <li>Rehab</li>
    <li>Foreclosures</li>
    <li>Short sales</li>
    <li>Development</li>
    <li>Finical modeling</li>
    <li>HUD properties</li>
    <li>Due Diligence e</li>
  </ul>
  <footer class="footer">FOOTER</footer>
</main>
</body>
</html>
```